Business card for Luxury Portable Restroom Trailer company

We are a Luxury Portable Restroom Trailer Company Called FALCRIDGE HIRES. Based in Orange County California. We provide portable restroom trailers for events, such as, Weddings, Concerts, Charity events, Sporting events, Tournaments, Corporate events, ect. We rent and Sell the Luxury restrooms. Our colors are white, grey, and Orange. As you will see in the logo we uploaded.
There are 2 people in the company so the names and titles will change for the 3 people but card will remain the same. Here is the information for each Person: Dwight Penner CFO 555 318-0476
next Person: Leon Marchetti VP 555 318-0476
Next Person: Owen Marchetti CEO 555 318-0476
Information to include on the card: Luxury Restroom Trailers Rental and Sales. Weddings, Concerts, Charity, Sporting and Corp. Events.

```html
<!DOCTYPE html>
<html lang="en">
<head>
<meta charset="utf-8">
<title>Falcridge Hires – Business Card</title>
<link href="https://fonts.googleapis.com/css2?family=Saira+Condensed:wght@600&family=Source+Sans+3:wght@400;700;800&display=swap" rel="stylesheet">
<style>
  :root {
    --orange: #f26a24;
    --orange-faint: #fdeee4;
    --grey: #58585a;
    --text-grey: #4b4b4d;
    --white: #ffffff;
    --backdrop: #e9e9e9;
  }
  * { margin: 0; padding: 0; box-sizing: border-box; }
  html, body {
    width: 1200px; height: 1200px; overflow: hidden;
    background: var(--backdrop);
    font-family: "Source Sans 3", sans-serif;
  }
  .card {
    position: absolute;
    left: 232px;
    width: 736px;
    height: 452px;
    background: var(--white);
    overflow: hidden;
  }
  .card--front { top: 118px; }
  .card--back { top: 630px; border: 26px solid var(--orange); }

  /* front */
  .brand {
    position: absolute; left: 40px; top: 58px;
    display: flex; align-items: center; gap: 10px;
  }
  .brand__mark { width: 22px; height: 22px; background: var(--orange); }
  .brand__name {
    font-weight: 800; font-size: 34px; letter-spacing: 1px;
    color: var(--orange); line-height: 1;
  }
  .person {
    position: absolute; left: 40px; top: 236px;
    font-family: "Saira Condensed", sans-serif; font-weight: 600;
    font-size: 40px; line-height: 1; color: var(--orange);
    text-transform: uppercase; letter-spacing: 0.5px;
  }
  .contact {
    position: absolute; left: 40px; top: 284px;
    font-size: 29px; line-height: 1; color: var(--text-grey);
  }
  .contact__label { color: var(--orange); }
  .rule {
    position: absolute; left: 40px; top: 330px;
    width: 652px; height: 2px; background: var(--orange);
  }
  .services {
    position: absolute; left: 40px; top: 344px; width: 670px;
    font-size: 21.5px; line-height: 29px; color: var(--text-grey);
  }

  /* back */
  .back__decor {
    position: absolute; left: 50%; top: 50%;
    width: 660px; height: 660px; margin: -330px 0 0 -330px;
    border-radius: 50%; background: var(--orange-faint);
  }
  .back__brand {
    position: absolute; inset: 0;
    display: flex; align-items: center; justify-content: center; gap: 16px;
  }
  .back__mark { width: 40px; height: 40px; background: var(--grey); }
  .back__name {
    font-weight: 800; font-size: 58px; letter-spacing: 1.5px;
    color: var(--grey); line-height: 1;
  }
</style>
</head>
<body>
  <section class="card card--front">
    <div class="brand">
      <span class="brand__mark"></span>
      <span class="brand__name">FALCRIDGE HIRES</span>
    </div>
    <h1 class="person">Dwight Penner CFO</h1>
    <p class="contact"><span class="contact__label">CONTACT:</span> 555 318-0476</p>
    <div class="rule"></div>
    <p class="services">Luxury Restroom Trailers Rental and Sales. Weddings, Concerts, Charity, Sporting and Corp. Events.</p>
  </section>

  <section class="card card--back">
    <div class="back__decor"></div>
    <div class="back__brand">
      <span class="back__mark"></span>
      <span class="back__name">FALCRIDGE HIRES</span>
    </div>
  </section>
</body>
</html>
```